Health Wellbeing Beauty online Shop

I have attached a full spec, however in summary this is a new business startup selling skincare products.

We need a web design for new wellbeing website, selling skincare products so need an eCommerce solution . On the home page I would like these faces to dissolve into each other on a loop or use a honeycomb style transation.
You will need the option of being able to log into an account, either through lumigram, vexora, chirplo or create an account. For created accounts, obviously need the facility to be able to reset passwords, see previous orders, track current order, and maintain favourites.
It should be PC, mobile and tablet friendly.

Look and Feel
It should be an elegant, modern, professional, trendy, unisex website. It should look clean and calm. Am happy to try interesting and slightly unusual designs. I would also like to have chat functionality, either powered by talvuNchat or by Quo 58.
Websites I like are
https://www.nobel-radiance.example.co.uk/
https://www.mereminerals.example.co.uk/
http://www.brightdermis.example.com/

PLEASE DO USE YOUR KNOWELDGE OF WHAT WORKS FOR WEB DESIGN. YOU’RE THE EXPERT AND NEED YOUR EXPERTISE. CARTE BLANCHE TO DESIGN AS YOU SEE FIT. Please be creative, I need my site to stand out from the crowd.

Target Market(s)

Target Market
Middle aged women are our most common client, however, younger patients, both male and female, will often visit the site. In summary, I would like the site to appeal to all age brackets.

Industry/Entity Type

Business

Coding

Coded - Design and coding required

Number of Pages Required

4 page

Requirements
Must have
• Need shop to be exactly like shop on this link http://www.brightdermis.example.com/
Nice to have
• i would like something unique and creative

```html
<!DOCTYPE html>
<html lang="en">
<head>
<meta charset="utf-8">
<title>Aurelle – Skin Lightening Tablets</title>
<link href="https://fonts.googleapis.com/css2?family=Lustria&family=Open+Sans:wght@400;600&display=swap" rel="stylesheet">
<style>
:root{
  --gold:#f5c23f;
  --gold-deep:#c9a24a;
  --ink:#1f1f1f;
  --panel:#2b2b2b;
  --footer-left:#303030;
  --footer-right:#3a3a3a;
  --footer-base:#151515;
  --text:#333;
  --muted:#777;
  --line:#d6d6d6;
  --chirplo:#2a9ad6;
  --lumigram:#2c4a8c;
  --white:#fff;
  --serif:'Lustria', Georgia, serif;
  --sans:'Open Sans', Arial, sans-serif;
}
*{box-sizing:border-box;margin:0;padding:0}
html,body{width:1200px;height:2311px;overflow:hidden}
body{position:relative;background:var(--white);font-family:var(--sans);color:var(--text)}
.abs{position:absolute}

/* header */
.site-header{left:132px;top:9px;width:935px;height:199px;background:var(--ink)}
.brand{left:11px;top:13px;width:122px;height:122px;display:flex;align-items:center;justify-content:center;gap:6px}
.brand-dot{width:10px;height:10px;border-radius:50%;background:var(--gold-deep)}
.brand-name{font-family:var(--serif);color:var(--gold-deep);font-size:24px}
.auth-btn{top:23px;height:39px;color:var(--white);font-size:12px;font-weight:600;display:flex;align-items:center;justify-content:center}
.auth-chirplo{left:445px;width:147px;background:var(--chirplo)}
.auth-lumigram{left:599px;width:172px;background:var(--lumigram)}
.auth-create{left:777px;width:148px;background:var(--gold);color:var(--ink)}
.social-dot{top:93px;width:26px;height:26px;border-radius:50%}
.social-lumigram{left:513px;background:var(--lumigram)}
.social-chirplo{left:545px;background:var(--chirplo)}
.cart{left:592px;top:91px;color:var(--white);display:flex;gap:8px;align-items:center}
.cart-label{font-size:10px;text-align:right;line-height:1.2}
.cart-label b{display:block;font-weight:400;font-size:14px}
.cart-count{left:638px;top:85px;width:16px;height:16px;border-radius:50%;background:var(--gold);color:var(--ink);font-size:9px;text-align:center;line-height:16px}
.search{left:709px;top:88px;width:216px;height:40px;background:var(--white);display:flex;align-items:center;justify-content:space-between;padding:0 14px;font-size:12px;color:#666}
.main-nav{left:7px;top:151px;width:921px;height:40px;background:var(--white);display:flex;align-items:center;font-family:var(--serif);font-size:12px;color:var(--ink)}
.main-nav a{height:100%;display:flex;align-items:center;justify-content:center;text-decoration:none;color:inherit;padding:0 22px}
.main-nav a.active{background:var(--gold);width:184px}
.main-nav a:nth-child(2){width:170px}
.main-nav a:nth-child(3){width:180px}
.main-nav a:nth-child(4){width:162px}
.main-nav a:nth-child(5){width:92px}

/* hero mosaic */
.tile{position:absolute}
.tone-a{background:linear-gradient(160deg,#e9d2c2,#c9a58e)}
.tone-b{background:linear-gradient(160deg,#4a3a33,#d8b29b)}
.tone-c{background:linear-gradient(160deg,#6a4634,#3a2a24)}
.tone-d{background:linear-gradient(160deg,#d9b09a,#a27864)}
.tone-e{background:linear-gradient(160deg,#c9c2bd,#e6d4c8)}
.tone-f{background:linear-gradient(160deg,#2b221f,#caa28b)}

/* sidebar */
.side-title{font-family:var(--serif);font-size:27px;color:var(--ink)}
.filter-box{left:132px;width:200px;background:var(--panel);padding:0 8px 8px}
.filter-head{height:35px;display:flex;align-items:center;gap:8px;color:var(--white);font-size:12px}
.filter-list{background:var(--white);list-style:none;padding:12px 14px 4px}
.filter-list li{font-size:12px;color:var(--text);height:32px;display:flex;align-items:center;gap:9px}
.cat-item{left:132px;width:200px;height:36px;border:1px solid var(--line);display:flex;align-items:center;gap:9px;padding-left:12px;font-size:12px;color:var(--text)}
.cat-item.active{background:var(--panel);border-color:var(--panel);color:var(--white)}
.promo{left:132px;top:1360px;width:200px;height:239px;border:3px solid var(--ink);background:linear-gradient(180deg,#f4f4f4 0%,#f4f4f4 55%,#bfe0e6 55%,#bfe0e6 70%,#bcd58a 70%)}

/* shop */
.shop-title{left:371px;top:641px;font-family:var(--serif);font-size:27px;color:var(--ink)}
.sort{left:883px;top:644px;display:flex;align-items:center;gap:6px;font-size:10px}
.sort-select{width:136px;height:28px;border:1px solid #ccc;display:flex;align-items:center;justify-content:space-between;padding:0 8px;font-size:10px}
.product-grid{left:373px;top:692px;display:grid;grid-template-columns:repeat(3,223px);grid-auto-rows:372px;gap:12px}
.product-card{border:1px solid var(--line);position:relative;text-align:center}
.product-shot{position:absolute;left:72px;top:26px;width:78px;height:180px;border-radius:8px;background:linear-gradient(180deg,#f2f2f2 0%,#f2f2f2 18%,#b8621d 24%,#7a3a0f 100%)}
.product-name{position:absolute;left:18px;right:18px;top:218px;font-family:var(--serif);font-size:15px;line-height:21px;color:var(--ink)}
.product-price{position:absolute;left:0;right:0;top:286px;font-family:var(--serif);font-size:15px;color:#555}
.product-price small{font-family:var(--sans);font-size:11px}
.stars{position:absolute;left:0;right:0;top:313px;display:flex;justify-content:center;gap:3px}
.actions{position:absolute;left:0;right:0;top:340px;display:flex;justify-content:center;gap:18px;font-size:12px;color:#555}
.actions span{display:flex;align-items:center;gap:6px}

.pager{left:606px;top:1868px;display:flex;gap:5px}
.pager span{width:27px;height:27px;border-radius:50%;background:#e4e4e4;color:#888;font-size:10px;display:flex;align-items:center;justify-content:center}
.pager span.current{background:var(--gold);color:var(--ink)}

/* footer */
.footer-about{left:0;top:1933px;width:599px;height:280px;background:var(--footer-left)}
.footer-contact{left:599px;top:1933px;width:601px;height:280px;background:var(--footer-right)}
.footer-title{font-family:var(--serif);color:var(--gold);font-size:27px}
.footer-copy{font-size:11px;line-height:17.5px;color:#b5b5b5}
.footer-btn{border:1px solid #999;color:#ccc;font-size:11px;display:flex;align-items:center;justify-content:center;height:36px}
.contact-line{font-size:12px;color:var(--white)}
.footer-base{left:0;top:2213px;width:1200px;height:98px;background:var(--footer-base)}
.base-links{left:132px;top:2238px;font-size:10px;color:#bbb;display:flex;gap:10px}
.copyright{left:132px;top:2268px;font-size:10px;color:#bbb}
.pay-card{top:2243px;height:27px;background:var(--white);border-radius:2px;font-size:8px;color:var(--lumigram);display:flex;align-items:center;justify-content:center;font-weight:600}
.live-chat{left:679px;top:2267px;width:227px;height:44px;background:var(--gold);display:flex;align-items:center;justify-content:center;gap:10px;font-size:15px;color:var(--ink)}
.live-chat small{font-size:9px}
</style>
</head>
<body>

<header class="site-header abs">
  <div class="brand abs"><span class="brand-dot"></span><span class="brand-name">Aurelle</span></div>
  <div class="auth-btn auth-chirplo abs">Login with chirplo</div>
  <div class="auth-btn auth-lumigram abs">Login with lumigram</div>
  <div class="auth-btn auth-create abs">
    <svg width="12" height="12" viewBox="0 0 12 12" style="margin-right:6px"><path d="M2 9l1-3 5-5 2 2-5 5z" fill="none" stroke="#1f1f1f" stroke-width="1.3"/><path d="M1 11h10" stroke="#1f1f1f"/></svg>Create An Account</div>
  <span class="social-dot social-lumigram abs" aria-label="lumigram"></span>
  <span class="social-dot social-chirplo abs" aria-label="chirplo"></span>
  <div class="cart abs">
    <div class="cart-label">My Cart<b>$00.00</b></div>
    <svg width="36" height="30" viewBox="0 0 36 30"><rect x="2" y="6" width="32" height="22" rx="2" fill="none" stroke="#fff" stroke-width="2"/><path d="M2 13h32M2 20h32M10 6v22M18 6v22M26 6v22" stroke="#fff" stroke-width="1.5"/></svg>
  </div>
  <div class="cart-count abs">0</div>
  <div class="search abs">Search
    <svg width="14" height="14" viewBox="0 0 14 14"><circle cx="6" cy="6" r="4.5" fill="none" stroke="#333" stroke-width="1.8"/><path d="M9.5 9.5L13 13" stroke="#333" stroke-width="2"/></svg>
  </div>
  <nav class="main-nav abs">
    <a class="active">Skin Lightening Tablets</a>
    <a>Skin Lightening Creams</a>
    <a>Skin Lightening Soaps</a>
    <a>Skin Lightening Vials</a>
    <a>Contact</a>
    <a>About Us</a>
  </nav>
</header>

<section class="hero" aria-label="Portrait mosaic">
  <div class="tile tone-a" style="left:132px;top:211px;width:246px;height:256px" role="img" aria-label="Portrait of a fair-haired woman"></div>
  <div class="tile tone-d" style="left:132px;top:470px;width:246px;height:143px" role="img" aria-label="Portrait of a smiling young woman"></div>
  <div class="tile tone-f" style="left:383px;top:211px;width:184px;height:199px" role="img" aria-label="Portrait of a dark-haired woman"></div>
  <div class="tile tone-b" style="left:383px;top:413px;width:184px;height:200px" role="img" aria-label="Portrait of a brunette woman"></div>
  <div class="tile tone-c" style="left:570px;top:211px;width:112px;height:122px" role="img" aria-label="Close portrait of a woman"></div>
  <div class="tile tone-e" style="left:570px;top:336px;width:112px;height:115px" role="img" aria-label="Portrait of an older woman"></div>
  <div class="tile tone-c" style="left:570px;top:454px;width:121px;height:159px" role="img" aria-label="Portrait of a young woman"></div>
  <div class="tile tone-d" style="left:685px;top:211px;width:155px;height:122px" role="img" aria-label="Close portrait of a mature woman"></div>
  <div class="tile tone-d" style="left:685px;top:336px;width:155px;height:115px" role="img" aria-label="Portrait of a bearded man"></div>
  <div class="tile tone-a" style="left:694px;top:454px;width:122px;height:159px" role="img" aria-label="Portrait of a young man"></div>
  <div class="tile tone-b" style="left:843px;top:211px;width:224px;height:240px" role="img" aria-label="Portrait of a smiling woman"></div>
  <div class="tile tone-e" style="left:819px;top:454px;width:122px;height:159px" role="img" aria-label="Portrait of a woman with dark hair"></div>
  <div class="tile tone-d" style="left:944px;top:454px;width:123px;height:159px" role="img" aria-label="Portrait of an older man"></div>
</section>

<aside>
  <h2 class="side-title abs" style="left:132px;top:641px">Refine by</h2>
  <div class="filter-box abs" style="top:682px">
    <div class="filter-head">
      <svg width="10" height="8" viewBox="0 0 10 8"><path d="M1 1l3 3-3 3M5 1l3 3-3 3" fill="none" stroke="#fff" stroke-width="1.3"/></svg>Price Range</div>
    <ul class="filter-list">
      <li><svg width="5" height="8" viewBox="0 0 5 8"><path d="M1 1l3 3-3 3" fill="none" stroke="#555"/></svg>Highest review score</li>
      <li><svg width="5" height="8" viewBox="0 0 5 8"><path d="M1 1l3 3-3 3" fill="none" stroke="#555"/></svg>Price high to low</li>
      <li><svg width="5" height="8" viewBox="0 0 5 8"><path d="M1 1l3 3-3 3" fill="none" stroke="#555"/></svg>Price low to high</li>
    </ul>
  </div>

  <h2 class="side-title abs" style="left:132px;top:864px">Brand</h2>
  <div class="filter-box abs" style="top:906px">
    <div class="filter-head">
      <svg width="10" height="8" viewBox="0 0 10 8"><path d="M1 1l3 3-3 3M5 1l3 3-3 3" fill="none" stroke="#fff" stroke-width="1.3"/></svg>Brand name</div>
    <ul class="filter-list">
      <li><svg width="5" height="8" viewBox="0 0 5 8"><path d="M1 1l3 3-3 3" fill="none" stroke="#555"/></svg>Aenean et bibendum</li>
      <li><svg width="5" height="8" viewBox="0 0 5 8"><path d="M1 1l3 3-3 3" fill="none" stroke="#555"/></svg>Donec sagitti</li>
      <li><svg width="5" height="8" viewBox="0 0 5 8"><path d="M1 1l3 3-3 3" fill="none" stroke="#555"/></svg>Cras suscipit est</li>
    </ul>
  </div>

  <h2 class="side-title abs" style="left:132px;top:1087px">Categories</h2>
  <div class="cat-item active abs" style="top:1129px"><svg width="10" height="8" viewBox="0 0 10 8"><path d="M1 1l3 3-3 3M5 1l3 3-3 3" fill="none" stroke="#fff" stroke-width="1.3"/></svg>Skin Lightening Tablets</div>
  <div class="cat-item abs" style="top:1169px"><svg width="10" height="8" viewBox="0 0 10 8"><path d="M1 1l3 3-3 3M5 1l3 3-3 3" fill="none" stroke="#333" stroke-width="1.3"/></svg>Skin Lightening Creams</div>
  <div class="cat-item abs" style="top:1209px"><svg width="10" height="8" viewBox="0 0 10 8"><path d="M1 1l3 3-3 3M5 1l3 3-3 3" fill="none" stroke="#333" stroke-width="1.3"/></svg>Skin Lightening Soaps</div>
  <div class="cat-item abs" style="top:1249px"><svg width="10" height="8" viewBox="0 0 10 8"><path d="M1 1l3 3-3 3M5 1l3 3-3 3" fill="none" stroke="#333" stroke-width="1.3"/></svg>Skin Lightening Vials</div>
  <div class="cat-item abs" style="top:1289px"><svg width="10" height="8" viewBox="0 0 10 8"><path d="M1 1l3 3-3 3M5 1l3 3-3 3" fill="none" stroke="#333" stroke-width="1.3"/></svg>Skin Lightening Systems</div>

  <div class="promo abs" role="img" aria-label="Event promotion banner"></div>
</aside>

<main>
  <h1 class="shop-title abs">Shop</h1>
  <div class="sort abs">Sort by :
    <div class="sort-select">Highest review score
      <svg width="7" height="5" viewBox="0 0 7 5"><path d="M0 0h7L3.5 5z" fill="#333"/></svg></div>
  </div>

  <div class="product-grid abs">
    <article class="product-card">
      <div class="product-shot" role="img" aria-label="Amber bottle of tablets"></div>
      <h3 class="product-name">Cum sociis natoque penati bus et magnis dis parturi ent montes</h3>
      <p class="product-price">$00.00<small>/per bottle</small></p>
      <div class="stars"><svg width="92" height="15" viewBox="0 0 92 15"><g fill="#f0b90b"><path id="st" d="M7.5 0l2.2 4.8 5.3.5-4 3.5 1.2 5.2-4.7-2.8-4.7 2.8 1.2-5.2-4-3.5 5.3-.5z"/><use href="#st" x="19"/><use href="#st" x="38"/><use href="#st" x="57"/><use href="#st" x="76"/></g></svg></div>
      <div class="actions">
        <span><svg width="16" height="10" viewBox="0 0 16 10"><path d="M1 5c3-5 11-5 14 0-3 5-11 5-14 0z" fill="#555"/><circle cx="8" cy="5" r="2.2" fill="#fff"/></svg>Quick View</span>
        <span><svg width="14" height="12" viewBox="0 0 14 12"><path d="M0 1h2.5l2 7h7l2-5.5H4" fill="none" stroke="#555" stroke-width="1.5"/><circle cx="5.5" cy="10.5" r="1.2" fill="#555"/><circle cx="10.5" cy="10.5" r="1.2" fill="#555"/></svg>Buy Now</span>
      </div>
    </article>
    <article class="product-card">
      <div class="product-shot" role="img" aria-label="Amber bottle of tablets"></div>
      <h3 class="product-name">Cum sociis natoque penati bus et magnis dis parturi ent montes</h3>
      <p class="product-price">$00.00<small>/per bottle</small></p>
      <div class="stars"><svg width="92" height="15" viewBox="0 0 92 15"><g fill="#f0b90b"><use href="#st"/><use href="#st" x="19"/><use href="#st" x="38"/><use href="#st" x="57"/><use href="#st" x="76"/></g></svg></div>
      <div class="actions">
        <span><svg width="16" height="10" viewBox="0 0 16 10"><path d="M1 5c3-5 11-5 14 0-3 5-11 5-14 0z" fill="#555"/><circle cx="8" cy="5" r="2.2" fill="#fff"/></svg>Quick View</span>
        <span><svg width="14" height="12" viewBox="0 0 14 12"><path d="M0 1h2.5l2 7h7l2-5.5H4" fill="none" stroke="#555" stroke-width="1.5"/><circle cx="5.5" cy="10.5" r="1.2" fill="#555"/><circle cx="10.5" cy="10.5" r="1.2" fill="#555"/></svg>Buy Now</span>
      </div>
    </article>
    <article class="product-card">
      <div class="product-shot" role="img" aria-label="Amber bottle of tablets"></div>
      <h3 class="product-name">Cum sociis natoque penati bus et magnis dis parturi ent montes</h3>
      <p class="product-price">$00.00<small>/per bottle</small></p>
      <div class="stars"><svg width="92" height="15" viewBox="0 0 92 15"><g fill="#f0b90b"><use href="#st"/><use href="#st" x="19"/><use href="#st" x="38"/><use href="#st" x="57"/><use href="#st" x="76"/></g></svg></div>
      <div class="actions">
        <span><svg width="16" height="10" viewBox="0 0 16 10"><path d="M1 5c3-5 11-5 14 0-3 5-11 5-14 0z" fill="#555"/><circle cx="8" cy="5" r="2.2" fill="#fff"/></svg>Quick View</span>
        <span><svg width="14" height="12" viewBox="0 0 14 12"><path d="M0 1h2.5l2 7h7l2-5.5H4" fill="none" stroke="#555" stroke-width="1.5"/><circle cx="5.5" cy="10.5" r="1.2" fill="#555"/><circle cx="10.5" cy="10.5" r="1.2" fill="#555"/></svg>Buy Now</span>
      </div>
    </article>
    <article class="product-card">
      <div class="product-shot" role="img" aria-label="Amber bottle of tablets"></div>
      <h3 class="product-name">Cum sociis natoque penati bus et magnis dis parturi ent montes</h3>
      <p class="product-price">$00.00<small>/per bottle</small></p>
      <div class="stars"><svg width="92" height="15" viewBox="0 0 92 15"><g fill="#f0b90b"><use href="#st"/><use href="#st" x="19"/><use href="#st" x="38"/><use href="#st" x="57"/><use href="#st" x="76"/></g></svg></div>
      <div class="actions">
        <span><svg width="16" height="10" viewBox="0 0 16 10"><path d="M1 5c3-5 11-5 14 0-3 5-11 5-14 0z" fill="#555"/><circle cx="8" cy="5" r="2.2" fill="#fff"/></svg>Quick View</span>
        <span><svg width="14" height="12" viewBox="0 0 14 12"><path d="M0 1h2.5l2 7h7l2-5.5H4" fill="none" stroke="#555" stroke-width="1.5"/><circle cx="5.5" cy="10.5" r="1.2" fill="#555"/><circle cx="10.5" cy="10.5" r="1.2" fill="#555"/></svg>Buy Now</span>
      </div>
    </article>
    <article class="product-card">
      <div class="product-shot" role="img" aria-label="Amber bottle of tablets"></div>
      <h3 class="product-name">Cum sociis natoque penati bus et magnis dis parturi ent montes</h3>
      <p class="product-price">$00.00<small>/per bottle</small></p>
      <div class="stars"><svg width="92" height="15" viewBox="0 0 92 15"><g fill="#f0b90b"><use href="#st"/><use href="#st" x="19"/><use href="#st" x="38"/><use href="#st" x="57"/><use href="#st" x="76"/></g></svg></div>
      <div class="actions">
        <span><svg width="16" height="10" viewBox="0 0 16 10"><path d="M1 5c3-5 11-5 14 0-3 5-11 5-14 0z" fill="#555"/><circle cx="8" cy="5" r="2.2" fill="#fff"/></svg>Quick View</span>
        <span><svg width="14" height="12" viewBox="0 0 14 12"><path d="M0 1h2.5l2 7h7l2-5.5H4" fill="none" stroke="#555" stroke-width="1.5"/><circle cx="5.5" cy="10.5" r="1.2" fill="#555"/><circle cx="10.5" cy="10.5" r="1.2" fill="#555"/></svg>Buy Now</span>
      </div>
    </article>
    <article class="product-card">
      <div class="product-shot" role="img" aria-label="Amber bottle of tablets"></div>
      <h3 class="product-name">Cum sociis natoque penati bus et magnis dis parturi ent montes</h3>
      <p class="product-price">$00.00<small>/per bottle</small></p>
      <div class="stars"><svg width="92" height="15" viewBox="0 0 92 15"><g fill="#f0b90b"><use href="#st"/><use href="#st" x="19"/><use href="#st" x="38"/><use href="#st" x="57"/><use href="#st" x="76"/></g></svg></div>
      <div class="actions">
        <span><svg width="16" height="10" viewBox="0 0 16 10"><path d="M1 5c3-5 11-5 14 0-3 5-11 5-14 0z" fill="#555"/><circle cx="8" cy="5" r="2.2" fill="#fff"/></svg>Quick View</span>
        <span><svg width="14" height="12" viewBox="0 0 14 12"><path d="M0 1h2.5l2 7h7l2-5.5H4" fill="none" stroke="#555" stroke-width="1.5"/><circle cx="5.5" cy="10.5" r="1.2" fill="#555"/><circle cx="10.5" cy="10.5" r="1.2" fill="#555"/></svg>Buy Now</span>
      </div>
    </article>
    <article class="product-card">
      <div class="product-shot" role="img" aria-label="Amber bottle of tablets"></div>
      <h3 class="product-name">Cum sociis natoque penati bus et magnis dis parturi ent montes</h3>
      <p class="product-price">$00.00<small>/per bottle</small></p>
      <div class="stars"><svg width="92" height="15" viewBox="0 0 92 15"><g fill="#f0b90b"><use href="#st"/><use href="#st" x="19"/><use href="#st" x="38"/><use href="#st" x="57"/><use href="#st" x="76"/></g></svg></div>
      <div class="actions">
        <span><svg width="16" height="10" viewBox="0 0 16 10"><path d="M1 5c3-5 11-5 14 0-3 5-11 5-14 0z" fill="#555"/><circle cx="8" cy="5" r="2.2" fill="#fff"/></svg>Quick View</span>
        <span><svg width="14" height="12" viewBox="0 0 14 12"><path d="M0 1h2.5l2 7h7l2-5.5H4" fill="none" stroke="#555" stroke-width="1.5"/><circle cx="5.5" cy="10.5" r="1.2" fill="#555"/><circle cx="10.5" cy="10.5" r="1.2" fill="#555"/></svg>Buy Now</span>
      </div>
    </article>
    <article class="product-card">
      <div class="product-shot" role="img" aria-label="Amber bottle of tablets"></div>
      <h3 class="product-name">Cum sociis natoque penati bus et magnis dis parturi ent montes</h3>
      <p class="product-price">$00.00<small>/per bottle</small></p>
      <div class="stars"><svg width="92" height="15" viewBox="0 0 92 15"><g fill="#f0b90b"><use href="#st"/><use href="#st" x="19"/><use href="#st" x="38"/><use href="#st" x="57"/><use href="#st" x="76"/></g></svg></div>
      <div class="actions">
        <span><svg width="16" height="10" viewBox="0 0 16 10"><path d="M1 5c3-5 11-5 14 0-3 5-11 5-14 0z" fill="#555"/><circle cx="8" cy="5" r="2.2" fill="#fff"/></svg>Quick View</span>
        <span><svg width="14" height="12" viewBox="0 0 14 12"><path d="M0 1h2.5l2 7h7l2-5.5H4" fill="none" stroke="#555" stroke-width="1.5"/><circle cx="5.5" cy="10.5" r="1.2" fill="#555"/><circle cx="10.5" cy="10.5" r="1.2" fill="#555"/></svg>Buy Now</span>
      </div>
    </article>
    <article class="product-card">
      <div class="product-shot" role="img" aria-label="Amber bottle of tablets"></div>
      <h3 class="product-name">Cum sociis natoque penati bus et magnis dis parturi ent montes</h3>
      <p class="product-price">$00.00<small>/per bottle</small></p>
      <div class="stars"><svg width="92" height="15" viewBox="0 0 92 15"><g fill="#f0b90b"><use href="#st"/><use href="#st" x="19"/><use href="#st" x="38"/><use href="#st" x="57"/><use href="#st" x="76"/></g></svg></div>
      <div class="actions">
        <span><svg width="16" height="10" viewBox="0 0 16 10"><path d="M1 5c3-5 11-5 14 0-3 5-11 5-14 0z" fill="#555"/><circle cx="8" cy="5" r="2.2" fill="#fff"/></svg>Quick View</span>
        <span><svg width="14" height="12" viewBox="0 0 14 12"><path d="M0 1h2.5l2 7h7l2-5.5H4" fill="none" stroke="#555" stroke-width="1.5"/><circle cx="5.5" cy="10.5" r="1.2" fill="#555"/><circle cx="10.5" cy="10.5" r="1.2" fill="#555"/></svg>Buy Now</span>
      </div>
    </article>
  </div>

  <nav class="pager abs" aria-label="Pages">
    <span>«</span><span class="current">1</span><span>2</span><span>3</span><span>4</span><span>5</span><span>»</span>
  </nav>
</main>

<footer>
  <section class="footer-about abs">
    <h2 class="footer-title abs" style="left:132px;top:25px">About</h2>
    <p class="footer-copy abs" style="left:132px;top:68px;width:440px">Phasellus non sodales ipsum. Pellentesque ac nisi eu sem suscipit luctus. Duis commodo aliquam mi, non pellentesque est finibus vitae. Maecenas ut faucibus magna, eget volutpat lorem. Nunc vestibulum ut nunc ut tincidunt. Curabitur non ante porttitor lectus volutpat imperdiet interdum sit amet erat. Maecenas convallis erat massa, sit amet faucibus purus imperdiet sed. Sed tellus odio, ullamcorper sed elit consequat, pretium dictum dui. Morbi a euismod sapien, ac porttitor sem. Suspendisse molestie at urna quis accumsan. Suspendisse potenti. Integer id dui elementum, feugiat erat quis.</p>
    <div class="footer-btn abs" style="left:132px;top:211px;width:82px">Read more</div>
  </section>
  <section class="footer-contact abs">
    <h2 class="footer-title abs" style="left:46px;top:25px">Contact</h2>
    <p class="footer-copy abs" style="left:46px;top:68px;width:480px">Get in touch for expert confidential supplement advice, or for customer services.</p>
    <p class="contact-line abs" style="left:46px;top:92px">Calling from the UK - 0808 157 0421</p>
    <p class="contact-line abs" style="left:46px;top:114px">Calling from Overseas - +44 808 157 0421</p>
    <p class="footer-copy abs" style="left:46px;top:140px;width:480px">To contact us by email, please click the send us a message tab on the right.</p>
    <p class="contact-line abs" style="left:46px;top:161px">Our team is available&nbsp; - Monday - Friday: 8am until 18:00pm</p>
    <p class="footer-copy abs" style="left:46px;top:182px">Answerphone out of hours</p>
    <div class="footer-btn abs" style="left:46px;top:211px;width:113px">Quick Contact Us</div>
  </section>
  <section class="footer-base abs">
    <div class="base-links abs" style="left:132px;top:25px">
      <span>Skin Lightening Tablets</span><span>|</span><span>Skin Lightening Creams</span><span>|</span><span>Skin Lightening Soaps</span><span>|</span><span>Skin Lightening Vials</span><span>|</span><span>Contact</span><span>|</span><span>About Us</span>
    </div>
    <p class="copyright abs" style="left:132px;top:55px">Copyright ©&nbsp; 2016&nbsp; Aurelle.&nbsp;&nbsp; All rights reserved.</p>
    <div class="pay-card abs" style="left:909px;top:30px;width:35px">Payvia</div>
    <div class="pay-card abs" style="left:949px;top:30px;width:35px">Trovex</div>
    <div class="pay-card abs" style="left:990px;top:30px;width:35px">Zenta Flash</div>
    <div class="pay-card abs" style="left:1031px;top:30px;width:36px">Zenta</div>
  </section>
  <div class="live-chat abs">
    <svg width="20" height="16" viewBox="0 0 20 16"><path d="M2 1h11a1 1 0 011 1v7a1 1 0 01-1 1H7l-4 3v-3H2a1 1 0 01-1-1V2a1 1 0 011-1z" fill="#1f1f1f"/><path d="M15 5h3a1 1 0 011 1v6a1 1 0 01-1 1h-1v2l-3-2H9v-2" fill="#1f1f1f"/></svg>
    Live Chat with us <small>Quo 58</small>
  </div>
</footer>

</body>
</html>
```